Business Card Design

I already have a company logo for my company. I have a logo for the manufacturer we represent. I want a professional business card design.

```html
<!DOCTYPE html>
<html lang="en">
<head>
<meta charset="utf-8">
<title>Beacon Point LLC – Business Card</title>
<link href="https://fonts.googleapis.com/css2?family=Open+Sans:wght@400;600;700;800&display=swap" rel="stylesheet">
<style>
  :root {
    --page-bg: #e9e3d8;
    --card-bg: #f6f3ee;
    --card-edge: #d9d2c6;
    --brand-red: #d5141c;
    --brand-gold: #b48a34;
    --gold-deep: #9c7325;
    --ink: #2b2b2b;
    --muted: #d8d2c8;
    --white: #ffffff;
  }
  * { box-sizing: border-box; margin: 0; padding: 0; }
  html, body { width: 1200px; height: 1046px; overflow: hidden; }
  body {
    background: var(--page-bg);
    font-family: "Open Sans", Arial, sans-serif;
    display: flex; align-items: center; justify-content: center;
  }
  .card {
    position: relative;
    width: 1000px; height: 545px;
    background: var(--card-bg);
    border: 2px solid var(--card-edge);
    border-radius: 34px;
    overflow: hidden;
  }
  .brand {
    position: absolute; top: 105px; left: 0; right: 0;
    display: flex; align-items: center; justify-content: center; gap: 18px;
  }
  .brand-mark {
    width: 56px; height: 56px; background: var(--brand-red); border-radius: 6px;
  }
  .brand-name {
    font-weight: 800; font-size: 52px; color: var(--brand-red);
    letter-spacing: 1px; text-transform: uppercase;
  }
  .info-band {
    position: absolute; left: 0; right: 0; top: 330px; height: 124px;
    background: linear-gradient(90deg, var(--gold-deep) 0%, var(--brand-gold) 30%, var(--brand-gold) 52%, var(--brand-red) 56%, var(--brand-red) 100%);
  }
  .person {
    position: absolute; left: 0; width: 370px; top: 20px; text-align: right;
  }
  .person-name { font-weight: 700; font-size: 38px; color: var(--brand-red); line-height: 1.1; }
  .person-title { font-weight: 600; font-size: 25px; color: var(--muted); margin-top: 6px; }
  .band-mark {
    position: absolute; left: 445px; top: 22px; width: 100px; height: 80px;
    display: flex; flex-direction: column; align-items: center; justify-content: center; gap: 6px;
  }
  .band-mark-square { width: 36px; height: 36px; background: var(--white); border-radius: 4px; }
  .band-mark-name { font-weight: 700; font-size: 13px; color: var(--white); text-transform: uppercase; white-space: nowrap; }
  .contacts {
    position: absolute; left: 645px; top: 14px; list-style: none;
  }
  .contacts li {
    display: flex; align-items: center; gap: 14px;
    color: var(--white); font-size: 22px; line-height: 32px;
  }
  .contacts svg { width: 22px; height: 22px; flex: none; }
  .address {
    position: absolute; left: 0; right: 0; top: 470px; text-align: center;
    font-size: 24px; color: var(--ink);
  }
</style>
</head>
<body>
  <article class="card">
    <header class="brand">
      <span class="brand-mark"></span>
      <span class="brand-name">Beacon Point LLC</span>
    </header>

    <section class="info-band">
      <div class="person">
        <p class="person-name">Lena Novakova</p>
        <p class="person-title">Managing Director</p>
      </div>

      <div class="band-mark">
        <span class="band-mark-square"></span>
        <span class="band-mark-name">Beacon Point</span>
      </div>

      <ul class="contacts">
        <li>
          <svg viewBox="0 0 24 24" fill="none" stroke="#fff" stroke-width="2" stroke-linecap="round" stroke-linejoin="round"><path d="M5 3h4l2 5-2.5 1.5a11 11 0 0 0 6 6L16 13l5 2v4a2 2 0 0 1-2 2A16 16 0 0 1 3 5a2 2 0 0 1 2-2z"/></svg>
          (555) 014-2286
        </li>
        <li>
          <svg viewBox="0 0 24 24" fill="none" stroke="#fff" stroke-width="2" stroke-linejoin="round"><rect x="2" y="5" width="20" height="14" rx="2"/><path d="M2 7l10 7 10-7"/></svg>
          hello@beaconpoint.example
        </li>
        <li>
          <svg viewBox="0 0 24 24" fill="none" stroke="#fff" stroke-width="2"><circle cx="12" cy="12" r="10"/><path d="M2 12h20M12 2a15 15 0 0 1 0 20M12 2a15 15 0 0 0 0 20"/></svg>
          www.beaconpoint.example
        </li>
      </ul>
    </section>

    <p class="address">2140 Harbor Ridge Rd #12, Clearwater, FL 33755, USA</p>
  </article>
</body>
</html>
```